Professional Package for CPA Firm

We would like a stationery design for our new CPA Firm based in Atlanta, GA called 'Vale 8'. We work with investors to help grow investments, tax free. We would like the design to have a professional/minimal look with a 'wow' factor. We need 9.5″ x 4.125″, 9x12, and 10x13 mailing envelopes, business cards, and a letterhead. We have a logo that is already complete. For the letterhead, we would like to have space to put credentials at the bottom of the page

Industry/Entity Type

CPA, Accounting

```html
<!DOCTYPE html>
<html lang="en">
<head>
<meta charset="UTF-8">
<title>Vale 8 — Business Cards</title>
<link href="https://fonts.googleapis.com/css2?family=Open+Sans:wght@400;600;700&display=swap" rel="stylesheet">
<style>
  :root {
    --backdrop: #1f2022;
    --card-navy: #0e3652;
    --teal: #1fb6c6;
    --coral: #f2565a;
    --silver: #c9cdd1;
    --white: #ffffff;
  }
  * { box-sizing: border-box; margin: 0; padding: 0; }
  html, body {
    width: 1200px;
    height: 874px;
    overflow: hidden;
    background: var(--backdrop);
    font-family: "Open Sans", Arial, sans-serif;
  }
  .sheet {
    width: 1200px;
    height: 874px;
    display: flex;
    justify-content: center;
    align-items: center;
    gap: 90px;
  }
  .card {
    width: 410px;
    height: 717px;
    background: var(--card-navy);
    border-radius: 22px;
    display: flex;
    flex-direction: column;
    align-items: center;
    justify-content: center;
    text-align: center;
    color: var(--white);
  }

  /* Front */
  .brand {
    display: flex;
    align-items: center;
    gap: 14px;
  }
  .brand-dot {
    width: 18px;
    height: 18px;
    border-radius: 50%;
    background: var(--coral);
  }
  .brand-name {
    font-size: 58px;
    font-weight: 700;
    letter-spacing: 2px;
    color: var(--silver);
    line-height: 1;
  }
  .tagline {
    margin-top: 14px;
    font-size: 17px;
    letter-spacing: 2.5px;
    color: var(--silver);
  }

  /* Back */
  .card-back { justify-content: flex-start; padding-top: 150px; }
  .back-brand {
    font-size: 26px;
    font-weight: 700;
    letter-spacing: 1.5px;
    color: var(--silver);
  }
  .person-name {
    margin-top: 38px;
    font-size: 25px;
    font-weight: 400;
    letter-spacing: 1px;
    color: var(--teal);
  }
  .person-role {
    margin-top: 2px;
    font-size: 15px;
    color: var(--coral);
  }
  .divider {
    margin-top: 22px;
    width: 26px;
    height: 2px;
    background: var(--teal);
  }
  .address {
    margin-top: 24px;
    font-size: 15px;
    line-height: 1.45;
  }
  .contact-icons {
    margin-top: 22px;
    display: flex;
    gap: 6px;
  }
  .contact-icons svg { width: 18px; height: 18px; }
  .contact-lines {
    margin-top: 22px;
    font-size: 15px;
    line-height: 1.45;
  }
</style>
</head>
<body>
  <main class="sheet">
    <section class="card card-front">
      <div class="brand">
        <span class="brand-dot"></span>
        <span class="brand-name">VALE 8</span>
      </div>
      <p class="tagline">CPAs and Tax Advisors</p>
    </section>

    <section class="card card-back">
      <p class="back-brand">VALE 8</p>
      <h1 class="person-name">DANIEL REYES</h1>
      <p class="person-role">President</p>
      <div class="divider"></div>
      <p class="address">214 Birchwood Road<br>Atlanta, Georgia 30318</p>
      <div class="contact-icons">
        <svg viewBox="0 0 18 18" aria-label="Phone"><circle cx="9" cy="9" r="9" fill="var(--coral)"/><path d="M6 5l2 2-1 1c.6 1.2 1.8 2.4 3 3l1-1 2 2-1.5 1.5C8.5 13 5 9.5 4.5 6.5z" fill="var(--card-navy)"/></svg>
        <svg viewBox="0 0 18 18" aria-label="Mobile"><circle cx="9" cy="9" r="9" fill="var(--coral)"/><rect x="6.5" y="4.5" width="5" height="9" rx="1" fill="var(--card-navy)"/></svg>
        <svg viewBox="0 0 18 18" aria-label="Email"><circle cx="9" cy="9" r="9" fill="var(--coral)"/><rect x="5" y="6" width="8" height="6" fill="var(--card-navy)"/><path d="M5 6l4 3 4-3" stroke="var(--coral)" stroke-width="0.8" fill="none"/></svg>
        <svg viewBox="0 0 18 18" aria-label="Website"><circle cx="9" cy="9" r="9" fill="var(--coral)"/><circle cx="9" cy="9" r="4" fill="none" stroke="var(--card-navy)" stroke-width="1.3"/><path d="M5 9h8M9 5v8" stroke="var(--card-navy)" stroke-width="1"/></svg>
      </div>
      <p class="contact-lines">404-555-0142<br>404-555-0187<br>info@vale8.com<br>www.vale8.com</p>
    </section>
  </main>
</body>
</html>
```